Powerpoint template and intro presentation

I have a short presentation of 6 slides that I'd like to be made pretty, see attached below - called target companies Intro.

I'd also like a template incorporating my logo which I have attached below as well

I've attached a jpeg with the logo with white background that is the logo that I would like to incorporate.

Powerpoint and logo file has been uploaded

```html
<!DOCTYPE html>
<html lang="en">
<head>
<meta charset="utf-8">
<title>Charts 1 – Northvale</title>
<link rel="stylesheet" href="https://fonts.googleapis.com/css2?family=Comfortaa:wght@300;400&family=Didact+Gothic&display=swap">
<style>
  :root {
    --green: #76b82a;
    --green-dark: #5a9420;
    --charcoal: #45474a;
    --charcoal-dark: #2f3133;
    --green-light: #a9d47a;
    --green-light-dark: #8cb85f;
    --band: #c9e3a6;
    --rule-grey: #c8c8c8;
    --grid: #b5b5b5;
    --text: #5b5b5b;
    --slide: #ffffff;
    --backdrop: #ecebe8;
  }
  * { margin: 0; padding: 0; box-sizing: border-box; }
  html, body { width: 1200px; height: 1000px; overflow: hidden; background: var(--backdrop); }
  .canvas { position: relative; width: 1200px; height: 1000px; }
  .slide { position: absolute; left: 33px; top: 70px; width: 1135px; height: 852px; background: var(--slide); }
  .brand {
    position: absolute; left: 96px; top: 150px;
    display: flex; align-items: center; gap: 8px;
  }
  .brand-mark { width: 16px; height: 16px; border-radius: 50%; background: var(--green); }
  .brand-name {
    font-family: "Comfortaa", sans-serif; font-weight: 400; font-size: 21px;
    color: var(--text); line-height: 1;
  }
  .slide-title {
    position: absolute; left: 262px; top: 138px;
    font-family: "Comfortaa", sans-serif; font-weight: 400; font-size: 37px; color: var(--green);
    line-height: 1;
  }
  .chart-heading {
    position: absolute; top: 242px;
    font-family: "Comfortaa", sans-serif; font-weight: 300; font-size: 27px; color: var(--text);
    letter-spacing: 0.5px; line-height: 1;
  }
  .chart-heading.column { left: 100px; }
  .chart-heading.line { left: 620px; }
  .rule-band { position: absolute; height: 6px; background: var(--band); }
  .rule-thin { position: absolute; height: 2px; background: var(--rule-grey); }
  .charts { position: absolute; left: 0; top: 0; }
  .charts text { font-family: "Didact Gothic", sans-serif; fill: var(--text); }
  .axis-value { font-size: 26px; }
  .axis-category { font-size: 28px; }
  .legend-label { font-size: 27px; }
  .page-number { font-family: "Didact Gothic", sans-serif; font-size: 15px; fill: #ffffff; }
</style>
</head>
<body>
<div class="canvas">
  <div class="slide"></div>

  <div class="brand">
    <span class="brand-mark"></span>
    <span class="brand-name">Northvale</span>
  </div>

  <h1 class="slide-title">Charts 1</h1>
  <div class="rule-band" style="left:262px; top:188px; width:906px;"></div>
  <div class="rule-thin" style="left:262px; top:198px; width:906px;"></div>

  <h2 class="chart-heading column">Heading For Column Chart</h2>
  <h2 class="chart-heading line">Heading For Line Chart</h2>

  <div class="rule-band" style="left:33px; top:862px; width:1025px;"></div>
  <div class="rule-thin" style="left:33px; top:872px; width:1025px;"></div>

  <svg class="charts" width="1200" height="1000" viewBox="0 0 1200 1000" aria-label="Column chart and line chart">
    <g class="column-chart">
      <g stroke="var(--grid)" stroke-width="1">
        <line x1="170" y1="670" x2="420" y2="670"/>
        <line x1="170" y1="635.5" x2="420" y2="635.5"/>
        <line x1="170" y1="601" x2="420" y2="601"/>
        <line x1="170" y1="566.5" x2="420" y2="566.5"/>
        <line x1="170" y1="532" x2="420" y2="532"/>
        <line x1="170" y1="497.5" x2="420" y2="497.5"/>
        <line x1="170" y1="463" x2="420" y2="463"/>
        <line x1="170" y1="428.5" x2="420" y2="428.5"/>
        <line x1="170" y1="394" x2="420" y2="394"/>
        <line x1="170" y1="359.5" x2="420" y2="359.5"/>
        <line x1="170" y1="325" x2="420" y2="325"/>
        <line x1="170" y1="325" x2="170" y2="676"/>
        <line x1="163" y1="676" x2="413" y2="676"/>
        <line x1="413" y1="676" x2="420" y2="670"/>
      </g>
      <g class="axis-value" text-anchor="end">
        <text x="143" y="680">0</text>
        <text x="143" y="645">0.5</text>
        <text x="143" y="611">1</text>
        <text x="143" y="576">1.5</text>
        <text x="143" y="542">2</text>
        <text x="143" y="507">2.5</text>
        <text x="143" y="473">3</text>
        <text x="143" y="438">3.5</text>
        <text x="143" y="404">4</text>
        <text x="143" y="369">4.5</text>
        <text x="143" y="335">5</text>
      </g>
      <g>
        <rect x="182" y="373.3" width="13" height="296.7" fill="var(--green)"/><polygon points="195,373.3 199,370 199,670 195,670" fill="var(--green-dark)"/><polygon points="182,373.3 186,370 199,370 195,373.3" fill="var(--green-dark)"/>
        <rect x="242" y="497.5" width="13" height="172.5" fill="var(--green)"/><polygon points="255,497.5 259,494 259,670 255,670" fill="var(--green-dark)"/><polygon points="242,497.5 246,494 259,494 255,497.5" fill="var(--green-dark)"/>
        <rect x="302" y="428.5" width="13" height="241.5" fill="var(--green)"/><polygon points="315,428.5 319,425 319,670 315,670" fill="var(--green-dark)"/><polygon points="302,428.5 306,425 319,425 315,428.5" fill="var(--green-dark)"/>
        <rect x="362" y="359.5" width="13" height="310.5" fill="var(--green)"/><polygon points="375,359.5 379,356 379,670 375,670" fill="var(--green-dark)"/><polygon points="362,359.5 366,356 379,356 375,359.5" fill="var(--green-dark)"/>
      </g>
      <g>
        <rect x="196" y="504.4" width="12" height="165.6" fill="var(--charcoal)"/><polygon points="208,504.4 212,501 212,670 208,670" fill="var(--charcoal-dark)"/>
        <rect x="256" y="366.4" width="12" height="303.6" fill="var(--charcoal)"/><polygon points="268,366.4 272,363 272,670 268,670" fill="var(--charcoal-dark)"/>
        <rect x="316" y="545.8" width="12" height="124.2" fill="var(--charcoal)"/><polygon points="328,545.8 332,542 332,670 328,670" fill="var(--charcoal-dark)"/>
        <rect x="376" y="476.8" width="12" height="193.2" fill="var(--charcoal)"/><polygon points="388,476.8 392,473 392,670 388,670" fill="var(--charcoal-dark)"/>
      </g>
      <g>
        <rect x="209" y="532" width="13" height="138" fill="var(--green-light)"/><polygon points="222,532 226,529 226,670 222,670" fill="var(--green-light-dark)"/>
        <rect x="269" y="532" width="13" height="138" fill="var(--green-light)"/><polygon points="282,532 286,529 286,670 282,670" fill="var(--green-light-dark)"/>
        <rect x="329" y="463" width="13" height="207" fill="var(--green-light)"/><polygon points="342,463 346,460 346,670 342,670" fill="var(--green-light-dark)"/>
        <rect x="389" y="325" width="13" height="345" fill="var(--green-light)"/><polygon points="402,325 406,322 406,670 402,670" fill="var(--green-light-dark)"/>
      </g>
      <g class="axis-category" text-anchor="end">
        <text transform="translate(208 692) rotate(-45)">Category 1</text>
        <text transform="translate(268 692) rotate(-45)">Category 2</text>
        <text transform="translate(328 692) rotate(-45)">Category 3</text>
        <text transform="translate(388 692) rotate(-45)">Category 4</text>
      </g>
      <g>
        <rect x="455" y="505" width="14" height="14" fill="var(--green)"/>
        <rect x="455" y="548" width="14" height="14" fill="var(--charcoal)"/>
        <rect x="455" y="591" width="14" height="14" fill="var(--green-light)"/>
        <text class="legend-label" x="476" y="522">Series 1</text>
        <text class="legend-label" x="476" y="565">Series 2</text>
        <text class="legend-label" x="476" y="608">Series 3</text>
      </g>
    </g>

    <g class="line-chart">
      <g stroke="var(--grid)" stroke-width="1">
        <line x1="684" y1="620.3" x2="938" y2="620.3"/>
        <line x1="684" y1="557.7" x2="938" y2="557.7"/>
        <line x1="684" y1="495" x2="938" y2="495"/>
        <line x1="684" y1="432.3" x2="938" y2="432.3"/>
        <line x1="684" y1="369.7" x2="938" y2="369.7"/>
        <line x1="684" y1="307" x2="938" y2="307"/>
        <line x1="684" y1="307" x2="684" y2="683"/>
        <line x1="684" y1="683" x2="938" y2="683"/>
        <line x1="684" y1="683" x2="684" y2="689"/>
        <line x1="748" y1="683" x2="748" y2="689"/>
        <line x1="811" y1="683" x2="811" y2="689"/>
        <line x1="875" y1="683" x2="875" y2="689"/>
        <line x1="938" y1="683" x2="938" y2="689"/>
      </g>
      <g class="axis-value" text-anchor="end">
        <text x="660" y="693">0</text>
        <text x="660" y="630">1</text>
        <text x="660" y="568">2</text>
        <text x="660" y="505">3</text>
        <text x="660" y="442">4</text>
        <text x="660" y="380">5</text>
        <text x="660" y="317">6</text>
      </g>
      <g fill="none" stroke-width="3" stroke-linejoin="miter">
        <polyline points="716,413.5 779,526.3 843,463.7 907,401" stroke="var(--green)"/>
        <polyline points="716,532.6 779,407.3 843,570.2 907,507.5" stroke="var(--charcoal)"/>
        <polyline points="716,557.7 779,557.7 843,495 907,369.7" stroke="var(--green-light)"/>
      </g>
      <g class="axis-category" text-anchor="end">
        <text transform="translate(728 700) rotate(-45)">Category 1</text>
        <text transform="translate(791 700) rotate(-45)">Category 2</text>
        <text transform="translate(855 700) rotate(-45)">Category 3</text>
        <text transform="translate(919 700) rotate(-45)">Category 4</text>
      </g>
      <g stroke-width="3">
        <line x1="962" y1="512" x2="996" y2="512" stroke="var(--green)"/>
        <line x1="962" y1="555" x2="996" y2="555" stroke="var(--charcoal)"/>
        <line x1="962" y1="598" x2="996" y2="598" stroke="var(--green-light)"/>
      </g>
      <text class="legend-label" x="998" y="522">Series 1</text>
      <text class="legend-label" x="998" y="565">Series 2</text>
      <text class="legend-label" x="998" y="608">Series 3</text>
    </g>

    <circle cx="1094" cy="876" r="24" fill="var(--green)"/>
    <text class="page-number" x="1094" y="881" text-anchor="middle">9</text>
  </svg>
</div>
</body>
</html>
```